BOLD & MINIMALIST DESIGN NEEDED

We want a very bold but minimalistic business card design that is impactful and utilizes both sides of the business card. Our current logo is included for your use.

We want bold fonts and good use of negative space. We don't want the logo to overpower the design.

Target Market(s)

Professionals who are building new commercial buildings.

Industry/Entity Type

Construction

Contact Information for Business Card

Name, Title, email, office phone, cell phone, website

Font styles to use
Serif
Sans Serif

Requirements
Must have
• Bold design!

```html
<!DOCTYPE html>
<html lang="en">
<head>
<meta charset="utf-8">
<title>Ridgecrest Design + Build — Business Card</title>
<link rel="stylesheet" href="https://fonts.googleapis.com/css2?family=Roboto:wght@400;500;700;900&display=swap">
<style>
  :root {
    --stage: #e9e6e1;
    --card-white: #ffffff;
    --card-black: #141414;
    --pattern-dark: #1d1d1d;
    --pattern-light: #2a2a2a;
    --ink: #1a1a1a;
    --ink-soft: #3a3a3a;
    --rule: #7a7a7a;
    --accent: #8cc63f;
  }
  * { box-sizing: border-box; margin: 0; padding: 0; }
  html, body { width: 1200px; height: 931px; overflow: hidden; }
  body {
    background: var(--stage);
    font-family: "Roboto", Arial, sans-serif;
    color: var(--ink);
    position: relative;
  }
  .card {
    position: absolute;
    width: 580px;
    height: 332px;
    border-radius: 22px;
    overflow: hidden;
    box-shadow: 0 8px 24px rgba(0,0,0,0.18);
  }
  /* Back side */
  .card--back {
    left: 90px;
    top: 70px;
    background: var(--card-black);
  }
  .back-pattern {
    position: absolute;
    inset: 0;
    background: linear-gradient(135deg, var(--pattern-dark) 0%, var(--card-black) 55%, var(--pattern-light) 100%);
  }
  .back-brand {
    position: absolute;
    left: 50%;
    top: 50%;
    transform: translate(-50%, -50%);
    display: flex;
    align-items: center;
    gap: 10px;
  }
  .back-brand__dot {
    width: 12px;
    height: 12px;
    border-radius: 50%;
    background: var(--accent);
  }
  .back-brand__name {
    font-weight: 900;
    font-size: 22px;
    letter-spacing: 1px;
    color: #ffffff;
  }
  /* Front side */
  .card--front {
    left: 530px;
    top: 540px;
    background: var(--card-white);
  }
  .front-brand {
    position: absolute;
    left: 36px;
    top: 0;
    width: 250px;
    height: 100%;
    display: flex;
    flex-direction: column;
    justify-content: center;
    align-items: center;
    text-align: center;
  }
  .front-brand__name {
    font-weight: 900;
    font-size: 36px;
    line-height: 1.05;
    color: var(--ink);
    letter-spacing: 0.5px;
  }
  .front-brand__tag {
    font-weight: 900;
    font-size: 15px;
    letter-spacing: 4px;
    color: var(--ink);
    margin-top: 6px;
  }
  .divider {
    position: absolute;
    left: 300px;
    top: 60px;
    width: 1px;
    height: 212px;
    background: var(--rule);
  }
  .contact {
    position: absolute;
    left: 326px;
    top: 56px;
    width: 240px;
  }
  .contact__name {
    font-weight: 700;
    font-size: 22px;
    color: var(--accent);
  }
  .contact__title {
    font-size: 14px;
    color: var(--ink-soft);
    margin: 2px 0 12px;
  }
  .contact__list { list-style: none; }
  .contact__item {
    display: flex;
    align-items: center;
    gap: 10px;
    font-size: 13.5px;
    color: var(--ink);
    margin-bottom: 7px;
  }
  .contact__icon { width: 14px; height: 14px; flex: none; fill: var(--ink); }
  .contact__address {
    font-size: 13.5px;
    line-height: 1.35;
    color: var(--ink);
    margin-top: 12px;
    padding-left: 24px;
  }
</style>
</head>
<body>

  <section class="card card--back" aria-label="Card back">
    <div class="back-pattern" role="img" aria-label="Dark embossed repeating brand pattern"></div>
    <div class="back-brand">
      <span class="back-brand__dot"></span>
      <span class="back-brand__name">RIDGECREST</span>
    </div>
  </section>

  <section class="card card--front" aria-label="Card front">
    <div class="front-brand">
      <div class="front-brand__name">RIDGECREST</div>
      <div class="front-brand__tag">DESIGN + BUILD</div>
    </div>

    <div class="divider"></div>

    <div class="contact">
      <div class="contact__name">Daniel Carver</div>
      <div class="contact__title">Owner</div>
      <ul class="contact__list">
        <li class="contact__item">
          <svg class="contact__icon" viewBox="0 0 24 24" aria-hidden="true"><path d="M6.6 10.8a15.1 15.1 0 0 0 6.6 6.6l2.2-2.2c.3-.3.7-.4 1-.2 1.1.4 2.3.6 3.6.6.6 0 1 .4 1 1V20c0 .6-.4 1-1 1C10.6 21 3 13.4 3 4c0-.6.4-1 1-1h3.5c.6 0 1 .4 1 1 0 1.3.2 2.5.6 3.6.1.3 0 .7-.2 1z"/></svg>
          055-210 384 617
        </li>
        <li class="contact__item">
          <svg class="contact__icon" viewBox="0 0 24 24" aria-hidden="true"><path d="M3 8c0-2 4-4 9-4s9 2 9 4v2h-4V8.5c-1.3-.5-3-.8-5-.8s-3.7.3-5 .8V10H3zm3 3h12l2 9H4zm6 2a2.5 2.5 0 1 0 0 5 2.5 2.5 0 0 0 0-5z"/></svg>
          055-210 384 618
        </li>
        <li class="contact__item">
          <svg class="contact__icon" viewBox="0 0 24 24" aria-hidden="true"><path d="M2 5h20v14H2zm2 2v.5l8 5 8-5V7zm0 2.8V17h16V9.8l-8 5z"/></svg>
          info@ridgecrestbuild.com
        </li>
        <li class="contact__item">
          <svg class="contact__icon" viewBox="0 0 24 24" aria-hidden="true"><path d="M12 2a10 10 0 1 0 0 20 10 10 0 0 0 0-20zm0 2c1 0 2.3 1.9 2.8 5H9.2C9.7 5.9 11 4 12 4zM4.3 10h3.8a20 20 0 0 0 0 4H4.3a8 8 0 0 1 0-4zm4.9 5h5.6c-.5 3.1-1.8 5-2.8 5s-2.3-1.9-2.8-5zm6.7-1a20 20 0 0 0 0-4h3.8a8 8 0 0 1 0 4z"/></svg>
          www.ridgecrestbuild.com
        </li>
      </ul>
      <p class="contact__address">Address line goes here<br>45452, Country name</p>
    </div>
  </section>

</body>
</html>
```